Financial Services General Marketing Brochure

Need a brochure to help recipients understand what makes BWC unique and the services that we offer. Must match look/feel of website https://brightwellcustody.example Layouts should make it easy to read the content - content should not be crammed into a traditional size/layout. Please see attached creative brief for specifics.

Target Market(s)

Financial advisors and mature couples looking for trustee services.

Industry/Entity Type

Financial Service

Colors
34a7d8
ffc214

Requirements
Must have
• See Creative Brief

```html
<!DOCTYPE html>
<html lang="en">
<head>
<meta charset="utf-8">
<title>Brightwell Custody – Brochure Spread</title>
<link rel="stylesheet" href="https://fonts.googleapis.com/css2?family=Merriweather:ital,wght@0,400;0,700;1,400&family=Open+Sans:ital,wght@0,400;0,600;1,400&display=swap">
<style>
  :root {
    --paper: #ffffff;
    --edge: #dcdcdc;
    --heading-blue: #4f6f8c;
    --text-grey: #5b5b5b;
    --muted-grey: #6e6e6e;
    --brand-navy: #3f5f7d;
    --brand-orange: #f29a2e;
    --band-blue: rgba(72, 106, 140, 0.82);
    --meadow-light: #efe8d6;
    --meadow-mid: #e4dcc4;
    --photo-green: #8f9a5a;
    --photo-warm: #c9b896;
  }
  * { box-sizing: border-box; margin: 0; padding: 0; }
  html, body { width: 1200px; height: 641px; overflow: hidden; background: var(--paper); }
  body { position: relative; font-family: "Open Sans", Arial, sans-serif; color: var(--text-grey); }

  .fold-line {
    position: absolute; left: 600px; top: 0; width: 0; height: 641px;
    border-left: 1px dashed var(--edge);
  }
  .panel { position: absolute; overflow: hidden; }

  /* Inside left panel */
  .services-panel { left: 0; top: 20px; width: 600px; height: 343px; background: var(--paper); border-top: 1px solid var(--edge); }
  .advisory-photo {
    position: absolute; left: 272px; top: 0; width: 328px; height: 193px;
    background: linear-gradient(135deg, #eef0f0 0%, #cfd6dc 45%, #7f94ac 75%, #a9b9c9 100%);
  }
  .section { position: absolute; }
  .section h2 {
    font-family: "Merriweather", Georgia, serif; font-weight: 400;
    font-size: 16px; color: var(--heading-blue); line-height: 1.2; margin-bottom: 6px;
  }
  .section .lead { font-style: italic; font-size: 8.5px; line-height: 1.5; color: var(--muted-grey); }
  .section ul { list-style: none; margin-top: 10px; }
  .section li { font-size: 8.5px; line-height: 13px; color: var(--muted-grey); }
  .section ul.bulleted li::before { content: "•"; color: var(--heading-blue); margin-right: 5px; }
  .section ul.plain { margin-top: 0; }
  .offer { left: 35px; top: 32px; width: 230px; }
  .audience { left: 35px; top: 98px; }
  .approach { left: 35px; top: 180px; width: 260px; }
  .specialties { left: 318px; top: 205px; width: 260px; }

  /* Back panel */
  .contact-panel {
    left: 0; top: 363px; width: 600px; height: 257px;
    background: linear-gradient(180deg, #f4efe4 0%, var(--meadow-light) 45%, var(--meadow-mid) 100%);
  }
  .contact-panel .meadow-photo { position: absolute; inset: 0; background: radial-gradient(ellipse at 60% 55%, rgba(201,184,150,0.35), transparent 60%); }
  .brand-block { position: absolute; left: 0; right: 0; top: 36px; text-align: center; }
  .brand-mark { display: inline-flex; align-items: center; gap: 8px; }
  .brand-dot { width: 14px; height: 14px; border-radius: 50%; background: var(--brand-orange); }
  .brand-name { font-family: "Merriweather", Georgia, serif; font-weight: 700; font-size: 21px; color: var(--brand-navy); }
  .brand-rule { width: 90px; height: 1px; background: var(--brand-orange); margin: 18px auto 10px; }
  .contact-list { list-style: none; }
  .contact-list li { font-size: 15px; line-height: 25px; color: var(--text-grey); }

  /* Cover panel */
  .cover-panel { left: 602px; top: 20px; width: 598px; height: 600px; }
  .family-photo {
    position: absolute; inset: 0;
    background: linear-gradient(180deg, #6f7d4a 0%, var(--photo-green) 20%, var(--photo-warm) 45%, #d8cdb8 62%, #9fb070 90%, #86a24a 100%);
  }
  .cover-band {
    position: absolute; left: 0; top: 345px; width: 598px; height: 207px;
    background: var(--band-blue);
  }
  .tagline {
    position: absolute; left: 16px; top: 78px; width: 320px;
    font-family: "Merriweather", Georgia, serif; font-style: italic;
    font-size: 17px; line-height: 24px; color: #ffffff;
  }
  .band-divider { position: absolute; left: 338px; top: 82px; width: 1px; height: 44px; background: rgba(255,255,255,0.75); }
  .cover-brand { position: absolute; left: 366px; top: 92px; display: flex; align-items: center; gap: 8px; }
  .cover-brand .brand-name { color: #ffffff; font-size: 20px; }
</style>
</head>
<body>
  <div class="fold-line"></div>

  <section class="panel services-panel">
    <div class="advisory-photo" role="img" aria-label="Photo of an advisor reviewing documents with a mature couple on a sofa"></div>

    <div class="section offer">
      <h2>What We Offer</h2>
      <p class="lead">We specialize exclusively in the delivery of trustee and estate fiduciary services.</p>
    </div>

    <div class="section audience">
      <h2>Who We Serve</h2>
      <ul class="plain">
        <li>Families</li>
        <li>Professional Advisors</li>
        <li>Foundations</li>
      </ul>
    </div>

    <div class="section approach">
      <h2>How We Serve</h2>
      <p class="lead">Our expertise and experience is in family wealth.<br>In this regard, we serve in the following ways:</p>
      <ul class="bulleted">
        <li>Trustee (Trusts)</li>
        <li>Executor and Personal Representative (Will)</li>
        <li>Agent for Financial Affairs (Power of Attorney)</li>
        <li>Trust Protector</li>
        <li>Special Independent Trustee</li>
        <li>Consultant</li>
        <li>Expert Witness</li>
      </ul>
    </div>

    <div class="section specialties">
      <h2>Trust Specialties</h2>
      <p class="lead">The general types of trusts on which we serve as trustee:</p>
      <ul class="bulleted">
        <li>Family Trusts</li>
        <li>Charitable Trusts</li>
        <li>Family Foundations</li>
        <li>Life Insurance Trusts</li>
        <li>Retirement Trusts</li>
        <li>Special Needs Trusts</li>
      </ul>
    </div>
  </section>

  <section class="panel contact-panel">
    <div class="meadow-photo" role="img" aria-label="Faded photo of a mother and child walking through a sunny meadow"></div>
    <div class="brand-block">
      <div class="brand-mark">
        <span class="brand-dot"></span>
        <span class="brand-name">Brightwell Custody</span>
      </div>
      <div class="brand-rule"></div>
      <ul class="contact-list">
        <li>brightwellcustody.example</li>
        <li>555-014-2290</li>
        <li>info@brightwellcustody.example</li>
      </ul>
    </div>
  </section>

  <section class="panel cover-panel">
    <div class="family-photo" role="img" aria-label="Photo of a smiling three-generation family sitting together in the grass outdoors"></div>
    <div class="cover-band">
      <p class="tagline">Helping families protect and enrich a multi-generational heritage</p>
      <div class="band-divider"></div>
      <div class="cover-brand">
        <span class="brand-dot"></span>
        <span class="brand-name">Brightwell Custody</span>
      </div>
    </div>
  </section>
</body>
</html>
```